Marcus Delbridge Finance

Need a personal website advertising Equipment Finance,Business Finance,Commercial Finance, Construction Finance, Bridging Finance. Similar websites are www.corvalend.com.au / www.tarmivest.com.au / www.qbr7.com.au /wwwhalvecredit.com.au

Target Market(s)

Business People

Industry/Entity Type

Business

Number of Pages Required

3 page

Font styles to use
Serif
Sans Serif

Requirements
Must have
• All i want is a simple corporate looking website advertising Equipment Finance, Commercial Finance, Construction Finance, Business Finance, Bridging Finance,

```html
<!DOCTYPE html>
<html lang="en">
<head>
<meta charset="utf-8">
<title>Marcus Delbridge Finance</title>
<link rel="stylesheet" href="https://fonts.googleapis.com/css2?family=Roboto:wght@400;500;700&family=Open+Sans:wght@400;600&family=Roboto+Slab:wght@400;700&display=swap">
<style>
:root{
  --navy:#0d2d57;
  --navy-dark:#0a2447;
  --blue:#00a9ec;
  --sky:#eef6fd;
  --line:#dfe5ec;
  --text:#3d4650;
  --muted:#8b939c;
  --footer:#e3e7eb;
  --gold:#b59a52;
  --white:#fff;
}
*{box-sizing:border-box;margin:0;padding:0}
html,body{width:1200px;height:2476px;overflow:hidden}
body{font-family:"Open Sans",Arial,sans-serif;color:var(--text);background:var(--white);font-size:12px}
.wrap{width:900px;margin:0 auto;position:relative}
a{color:inherit;text-decoration:none}

/* top bar */
.topbar{height:38px;background:#f5f9fd;border-bottom:1px solid var(--line)}
.topbar .wrap{display:flex;height:38px;align-items:stretch}
.topbar-links{display:flex;margin-left:10px}
.topbar-links span{display:flex;align-items:center;justify-content:center;border-left:1px solid var(--line);padding:0 14px;color:var(--navy);font-size:11px}
.topbar-links span:last-child{border-right:1px solid var(--line)}
.topbar-links .dot{width:38px;padding:0}
.topbar-links .dot i{width:12px;height:12px;border-radius:50%;background:var(--navy);display:block}
.quote-tab{margin-left:auto;align-self:flex-end;height:30px;width:118px;background:var(--navy);color:#fff;font-family:Roboto,sans-serif;font-size:12px;display:flex;align-items:center;justify-content:center;clip-path:polygon(8% 0,92% 0,100% 100%,0 100%)}

/* header */
.header{height:79px}
.header .wrap{display:flex;align-items:center;height:79px}
.brand{font-family:"Roboto Slab",serif;font-weight:700;color:var(--navy);font-size:19px;line-height:1.05;width:180px}
.main-nav{display:flex;gap:30px;margin-left:3px;font-family:Roboto,sans-serif;font-size:11px;color:var(--navy);text-transform:uppercase}
.main-nav .active{color:var(--blue);position:relative}
.main-nav .active::after{content:"";position:absolute;left:0;right:0;bottom:-9px;height:2px;background:var(--blue)}
.header-phone{margin-left:auto;font-family:Roboto,sans-serif;font-size:23px;color:var(--navy)}

/* service nav */
.service-nav{height:36px;background:var(--blue)}
.service-nav .wrap{display:flex;gap:40px;height:36px;align-items:center;color:#fff;font-family:Roboto,sans-serif;font-size:12.5px}

/* hero */
.hero{height:377px;position:relative;overflow:hidden}
.hero-photo{position:absolute;inset:0;background:linear-gradient(90deg,#b6d3ea 0%,#d8e9f5 35%,#eef5fb 60%,#dce8f2 80%,#c3d4e3 100%)}
.hero-text{position:absolute;left:162px;top:90px}
.hero h1{font-family:Roboto,sans-serif;font-weight:700;font-size:36px;color:var(--navy);letter-spacing:.3px}
.hero p{font-family:Roboto,sans-serif;font-size:22px;line-height:27px;color:var(--navy);text-transform:uppercase;margin-top:6px;width:520px}
.btn-navy{display:inline-flex;align-items:center;gap:10px;background:var(--navy);color:#fff;font-family:Roboto,sans-serif;font-size:12px;text-transform:uppercase;height:36px;padding:0 22px}
.hero .btn-navy{margin-top:38px;width:151px}

/* partners */
.partners{height:81px;border-bottom:1px solid var(--line);width:900px;margin:0 auto;display:flex;align-items:center;justify-content:space-between;padding:0 30px}
.partners span{font-family:Roboto,sans-serif;font-weight:700;font-size:14px;color:#4a5563}

/* welcome */
.welcome{height:222px;text-align:center;padding-top:42px}
.welcome h2{font-family:Roboto,sans-serif;font-weight:400;font-size:34px;color:var(--navy)}
.welcome p{width:900px;margin:18px auto 0;font-size:10.5px;line-height:14.5px;color:#4b535b}

/* services */
.services{height:550px;background:var(--sky);padding-top:83px}
.grid{width:900px;margin:0 auto;display:grid;grid-template-columns:repeat(3,1fr);gap:2px;background:var(--sky)}
.card{background:#fff;height:192px;text-align:center;padding-top:18px}
.card svg{display:block;margin:0 auto}
.card h3{font-family:Roboto,sans-serif;font-weight:400;font-size:14px;color:#1c2530;margin-top:12px}
.card .rule{width:60px;height:1px;background:var(--line);margin:10px auto}
.card p{font-size:10px;line-height:12.5px;color:var(--muted);width:210px;margin:0 auto}
.card.cta{background:var(--blue);color:#fff;padding-top:30px}
.cta .lead{font-family:Roboto,sans-serif;font-size:13px}
.cta .num{font-family:Roboto,sans-serif;font-size:22px;margin-top:12px}
.cta p{color:#fff;margin-top:10px;width:200px}
.cta .btn-navy{margin-top:14px;height:34px;padding:0 42px;font-size:11px}

/* about */
.about{height:383px;width:900px;margin:0 auto;position:relative;border-bottom:1px solid var(--line)}
.about-photo{position:absolute;left:13px;top:-34px;width:240px;height:416px;background:linear-gradient(160deg,#e3e8ee 0%,#b9c2cc 55%,#8e98a5 100%)}
.about-body{position:absolute;left:272px;top:11px;width:627px}
.about-bar{height:44px;background:var(--navy);color:#fff;font-family:Roboto,sans-serif;font-size:17px;display:flex;align-items:center;padding-left:18px;border-left:5px solid var(--blue)}
.about-main{position:absolute;left:0;top:64px;width:455px}
.about-main .kicker{font-family:Roboto,sans-serif;color:var(--blue);font-size:15px;padding-left:4px}
.about-main .sub{font-family:Roboto,sans-serif;color:#1e2833;font-size:15px;margin-top:4px;padding-left:4px}
.about-main p{font-size:11.5px;line-height:20px;color:#4b535b;margin-top:6px;padding-left:4px}
.btn-blue{display:inline-flex;align-items:center;gap:10px;background:var(--blue);color:#fff;font-family:Roboto,sans-serif;font-size:13px;height:36px;padding:0 22px;margin-top:18px}
.achieve{position:absolute;left:473px;top:64px;width:154px;border-left:1px solid var(--line);text-align:center}
.achieve h4{font-family:Roboto,sans-serif;font-weight:500;font-size:16px;color:var(--navy)}
.achieve .notch{width:120px;margin:6px auto 0;height:12px;border-top:1px solid var(--line);position:relative}
.achieve svg{display:block;margin:18px auto 0}

/* posts */
.posts{height:453px;padding-top:61px}
.posts .wrap{display:grid;grid-template-columns:repeat(3,300px)}
.post{text-align:center}
.post-img{height:222px}
.post h3{font-family:Roboto,sans-serif;font-weight:400;font-size:15px;color:#1c2530;margin-top:12px}
.post .rule{width:70px;height:1px;background:var(--line);margin:10px auto}
.post p{font-size:10px;line-height:12.5px;color:var(--muted);width:250px;margin:0 auto}
.post .more{color:var(--blue);font-size:11px;margin-top:8px;display:block}

/* footer */
.footer{height:185px;background:var(--footer);padding-top:42px}
.footer .wrap{display:flex}
.footer ul{list-style:none;font-family:Roboto,sans-serif;font-size:10.5px;color:var(--navy);text-transform:uppercase;line-height:22.5px}
.foot-services{margin-left:18px;width:265px}
.foot-links{width:175px}
.subscribe h5{font-family:Roboto,sans-serif;font-weight:400;font-size:11px;color:var(--navy);text-transform:uppercase}
.subscribe-row{display:flex;gap:18px;margin-top:8px;align-items:flex-end}
.subscribe-row .field{width:253px;height:35px;background:#fff;border:1px solid #d5dae0;font-size:10px;color:#666;display:flex;align-items:center;padding-left:10px}
.subscribe-row .btn{width:144px;height:35px;background:var(--blue);color:#fff;font-family:Roboto,sans-serif;font-size:13px;display:flex;align-items:center;justify-content:center;text-transform:uppercase;margin-bottom:-17px}
.foot-social{display:flex;gap:7px;margin-top:13px}
.foot-social i{width:24px;height:24px;border-radius:50%;background:var(--navy-dark);display:block}
.copyright{height:72px;display:flex;align-items:center;justify-content:center;font-size:9.5px;color:#333}
</style>
</head>
<body>

<div class="topbar">
  <div class="wrap">
    <div class="topbar-links">
      <span>Contact Us</span>
      <span class="dot"><i></i></span>
      <span class="dot"><i></i></span>
      <span class="dot"><i></i></span>
      <span class="dot"><i></i></span>
    </div>
    <a class="quote-tab">QUICK QUOTE</a>
  </div>
</div>

<header class="header">
  <div class="wrap">
    <div class="brand">Marcus Delbridge<br>Finance</div>
    <nav class="main-nav">
      <a class="active">Home</a>
      <a>About Marcus</a>
      <a>Contact</a>
    </nav>
    <div class="header-phone">555-014-2290</div>
  </div>
</header>

<nav class="service-nav">
  <div class="wrap">
    <a>Equipment Finance</a><a>Commercial Finance</a><a>Construction Finance</a><a>Business Finance</a><a>Bridging Finance</a>
  </div>
</nav>

<section class="hero">
  <div class="hero-photo" role="img" aria-label="Photo: glass office tower and blurred business people behind a smiling advisor offering a handshake"></div>
  <div class="hero-text">
    <h1>FINANCE SOLUTIONS</h1>
    <p>Lorem ipsum dolor sit amet, consectetur adipiscing elit. Sed euismod odio</p>
    <a class="btn-navy"><svg width="16" height="8" viewBox="0 0 16 8"><path d="M0 4h14M11 1l3 3-3 3" stroke="#fff" stroke-width="1.4" fill="none"/></svg>Get Quote</a>
  </div>
</section>

<div class="partners">
  <span>Arlen</span><span>Kestrel Bank</span><span>Norvane</span><span>Ollisar</span><span>Brackwell Capital</span><span>Tamsin Money</span><span>Veltra</span>
</div>

<section class="welcome">
  <h2>Welcome</h2>
  <p>Lorem ipsum dolor sit amet, consectetur adipiscing elit. Sed vel semper risus, id consequat mauris. Curabitur sit amet accumsan est, at sollicitudin nunc. Nullam semper at nulla eget dictum. Fusce mollis laoreet mattis. Suspendisse eget sagittis dolor. Phasellus facilisis quam dolor. Donec ac odio et justo ultricies efficitur at pharetra sem. Sed blandit, velit in tristique volutpat, libero mi pellentesque dolor, sed porta eros lacus ut odio. Etiam tempus ipsum justo, eget faucibus augue dignissim ac. Phasellus sit amet vulputate felis. Proin ligula ante, porta id posuere in, finibus sit amet mauris.</p>
</section>

<section class="services">
  <div class="grid">
    <div class="card">
      <svg width="44" height="40" viewBox="0 0 44 40" fill="none" stroke="#00a9ec" stroke-width="2.4"><rect x="6" y="12" width="16" height="18"/><path d="M22 30h10V4M32 30h10"/><circle cx="10" cy="34" r="4"/><circle cx="24" cy="34" r="4"/></svg>
      <h3>Equipment Finance</h3><div class="rule"></div>
      <p>Lorem ipsum dolor sit amet, consectetur adipiscing elit. Sed euismod odio vitae orci tempor, eget egestas nunc condimentum.</p>
    </div>
    <div class="card">
      <svg width="44" height="40" viewBox="0 0 44 40" fill="#00a9ec"><rect x="4" y="26" width="7" height="12"/><rect x="14" y="20" width="7" height="18"/><rect x="24" y="14" width="7" height="24"/><rect x="34" y="8" width="7" height="30"/><path d="M4 18L16 10l8 5 14-11" stroke="#00a9ec" stroke-width="2" fill="none"/></svg>
      <h3>Commercial Finance</h3><div class="rule"></div>
      <p>Lorem ipsum dolor sit amet, consectetur adipiscing elit. Sed euismod odio vitae orci tempor, eget egestas nunc condimentum.</p>
    </div>
    <div class="card">
      <svg width="44" height="40" viewBox="0 0 44 40" fill="none" stroke="#00a9ec" stroke-width="2.2"><rect x="12" y="3" width="20" height="35"/><path d="M17 10h3M24 10h3M17 17h3M24 17h3M17 24h3M24 24h3M19 38v-7h6v7"/></svg>
      <h3>Construction Finance</h3><div class="rule"></div>
      <p>Lorem ipsum dolor sit amet, consectetur adipiscing elit. Sed euismod odio vitae orci tempor, eget egestas nunc condimentum.</p>
    </div>
    <div class="card">
      <svg width="48" height="40" viewBox="0 0 48 40" fill="#00a9ec"><path d="M2 12l10-4 8 4 8-4 8 2 10-2v16l-8 2-8 8-6-2-6 2-8-8-8-2z"/></svg>
      <h3>Business Finance</h3><div class="rule"></div>
      <p>Lorem ipsum dolor sit amet, consectetur adipiscing elit. Sed euismod odio vitae orci tempor, eget egestas nunc condimentum.</p>
    </div>
    <div class="card">
      <svg width="48" height="40" viewBox="0 0 48 40" fill="none" stroke="#00a9ec" stroke-width="2.2"><rect x="3" y="6" width="30" height="26"/><path d="M3 13h30M10 2v7M26 2v7M9 19h4M16 19h4M23 19h4M9 25h4M16 25h4"/><rect x="28" y="26" width="18" height="11" fill="#fff"/></svg>
      <h3>Bridging Finance</h3><div class="rule"></div>
      <p>Lorem ipsum dolor sit amet, consectetur adipiscing elit. Sed euismod odio vitae orci tempor, eget egestas nunc condimentum.</p>
    </div>
    <div class="card cta">
      <div class="lead">For More Info Call:</div>
      <div class="num">555-014-2290</div>
      <p>Lorem ipsum dolor sit amet, consectetur adipiscing elit.</p>
      <a class="btn-navy">Quick Quote</a>
    </div>
  </div>
</section>

<section class="about">
  <div class="about-photo" role="img" aria-label="Portrait photo of Marcus Delbridge"></div>
  <div class="about-body">
    <div class="about-bar">Meet Marcus Delbridge</div>
    <div class="about-main">
      <div class="kicker">Proin id vestibulum libero.</div>
      <div class="sub">Morbi vel eros pulvinar aliquam fermentum convallis risus.</div>
      <p>Lorem ipsum dolor sit amet, consectetur adipiscing elit. In faucibus pellentesque massa, non scelerisque arcu dapibus in. Lorem ipsum dolor sit amet, consectetur adipiscing elit. Nullam gravida, libero eget vestibulum ultricies, odio lacus lobortis lorem, fringilla vehicula nunc dolor ut turpis. Donec sit amet nibh luctus, imperdiet metus eget, bibendum sapien. Vestibulum porta, diam nec volutpat dignissim, massa diam dignissim arcu, dictum auctor risus leo varius purus. Suspendisse gravida vehicula orci in malesuada. Aliquam sagittis lacinia diam ut rutrum. Vivamus placerat justo et mauris imperdiet imperdiet.</p>
      <a class="btn-blue"><svg width="8" height="9" viewBox="0 0 8 9"><path d="M0 0l8 4.5L0 9z" fill="#fff"/></svg>Full Bio</a>
    </div>
    <div class="achieve">
      <h4>Achievements</h4>
      <div class="notch"></div>
      <svg width="84" height="84" viewBox="0 0 84 84"><circle cx="42" cy="42" r="40" fill="#b59a52"/></svg>
      <svg width="84" height="124" viewBox="0 0 84 124"><path d="M2 6h80v94L42 122 2 100z" fill="#00a9ec"/></svg>
    </div>
  </div>
</section>

<section class="posts">
  <div class="wrap">
    <article class="post">
      <div class="post-img" role="img" aria-label="Photo: person in a hooded top working on a laptop" style="background:linear-gradient(135deg,#e4e7ea,#b9bfc6 55%,#eef0f2)"></div>
      <h3>In aliquam tortor et nunc maximus</h3><div class="rule"></div>
      <p>Lorem ipsum dolor sit amet, consectetur adipiscing elit. Sed euismod odio vitae orci tempor, eget egestas nunc condimentum.</p>
      <span class="more">- Read more</span>
    </article>
    <article class="post">
      <div class="post-img" role="img" aria-label="Photo: overhead view of business people at a desk with a laptop and paperwork" style="background:linear-gradient(135deg,#8fa6bf,#d8dfe6 45%,#5f7690)"></div>
      <h3>In aliquam tortor et nunc maximus</h3><div class="rule"></div>
      <p>Lorem ipsum dolor sit amet, consectetur adipiscing elit. Sed euismod odio vitae orci tempor, eget egestas nunc condimentum.</p>
      <span class="more">- Read more</span>
    </article>
    <article class="post">
      <div class="post-img" role="img" aria-label="Photo: customer support team wearing headsets in a bright office" style="background:linear-gradient(135deg,#f3f5f7,#d3dbe3 55%,#eef1f4)"></div>
      <h3>In aliquam tortor et nunc maximus</h3><div class="rule"></div>
      <p>Lorem ipsum dolor sit amet, consectetur adipiscing elit. Sed euismod odio vitae orci tempor, eget egestas nunc condimentum.</p>
      <span class="more">- Read more</span>
    </article>
  </div>
</section>

<footer class="footer">
  <div class="wrap">
    <ul class="foot-services">
      <li>Equipment Finance</li><li>Commercial Finance</li><li>Construction Finance</li><li>Business Finance</li><li>Bridging Finance</li>
    </ul>
    <ul class="foot-links">
      <li>Home</li><li>About Marcus</li><li>Contact</li>
    </ul>
    <div class="subscribe">
      <h5>Subscribe for the latest news</h5>
      <div class="subscribe-row">
        <div class="field">Enter Your Email</div>
        <div class="btn">Subscribe</div>
      </div>
      <div class="foot-social"><i></i><i></i><i></i><i></i></div>
    </div>
  </div>
</footer>

<div class="copyright">Copyright 2017 delbridgefinance.example All Rights Reserved.</div>

</body>
</html>
```